Harborline Claim Partners Business card

We need to get business card Design for our Company we are Public Adjusters in Chicago Illinois - i like to see good combination and elements from my Company Logo. as well To be an two side design
Updates

Target Market(s)

Home /Business owner Property Managers

Industry/Entity Type

Business

Contact Information for Business Card

to show the Element of our logo i will Like 3D

Font styles to use
Sans Serif

Requirements
Must have
• Logo and Element of the Logo in 3D
Nice to have
• Logo That we Provide 3D Same Colors or open for suggestions
Should not have
• unleare view -

```html
<!DOCTYPE html>
<html lang="en">
<head>
<meta charset="utf-8">
<title>Harborline Claim Partners — Business Card</title>
<link href="https://fonts.googleapis.com/css2?family=Open+Sans:wght@400;600;700&display=swap" rel="stylesheet">
<style>
  :root {
    --backdrop: #5b4b3d;
    --card-white: #ffffff;
    --brand-blue: #1a2fb8;
    --brand-red: #d8452f;
    --ink-grey: #555555;
    --rule-grey: #cfcfcf;
    --navy-deep: #0f0f4d;
    --navy-mid: #1b2a8f;
    --royal: #0b44c8;
    --white: #ffffff;
  }
  * { margin: 0; padding: 0; box-sizing: border-box; }
  html, body {
    width: 1200px; height: 987px; overflow: hidden;
    background: var(--backdrop);
    font-family: "Open Sans", Arial, sans-serif;
  }
  .canvas { position: relative; width: 1200px; height: 987px; }

  .card {
    position: absolute; width: 615px; height: 352px;
    box-shadow: 0 2px 6px rgba(0,0,0,.35);
    overflow: hidden;
  }

  /* Front side */
  .card-front { left: 293px; top: 130px; background: var(--card-white); }
  .front-brand {
    position: absolute; top: 86px; left: 0; width: 100%;
    display: flex; align-items: center; justify-content: center; gap: 10px;
  }
  .brand-dot {
    width: 26px; height: 26px; border-radius: 50%;
    background: var(--brand-blue);
  }
  .front-brand .brand-name {
    font-size: 21px; font-weight: 700; color: var(--brand-blue); letter-spacing: .2px;
  }
  .holder {
    position: absolute; right: 326px; top: 168px; text-align: right;
  }
  .holder-name { font-size: 21px; font-weight: 600; color: var(--brand-blue); line-height: 28px; }
  .holder-role { font-size: 17px; color: var(--brand-red); line-height: 24px; }
  .holder-address { font-size: 15.5px; color: var(--ink-grey); line-height: 23px; }
  .front-divider {
    position: absolute; left: 309px; top: 163px; width: 1px; height: 105px;
    background: var(--rule-grey);
  }
  .contacts { position: absolute; left: 328px; top: 171px; list-style: none; }
  .contacts li {
    display: flex; align-items: center; gap: 8px;
    font-size: 15.5px; color: var(--ink-grey); height: 23.5px;
  }
  .contacts svg { width: 15px; height: 15px; fill: var(--brand-blue); flex: none; }
  .web-band {
    position: absolute; left: 0; top: 306px; width: 100%; height: 30px;
    background: linear-gradient(90deg, var(--navy-deep) 0%, var(--navy-mid) 50%, var(--navy-deep) 100%);
    display: flex; align-items: center; justify-content: center;
    color: var(--white); font-size: 15px; letter-spacing: 6px;
  }

  /* Back side */
  .card-back {
    left: 292px; top: 505px;
    background: radial-gradient(ellipse 60% 75% at 50% 50%, var(--royal) 0%, #0a2f9a 45%, var(--navy-deep) 100%);
  }
  .back-brand {
    position: absolute; top: 150px; left: 0; width: 100%;
    display: flex; align-items: center; justify-content: center; gap: 12px;
  }
  .back-brand .brand-dot { width: 34px; height: 34px; background: var(--white); }
  .back-brand .brand-name { font-size: 25px; font-weight: 700; color: var(--white); }
  .back-rule {
    position: absolute; left: 83px; top: 271px; width: 451px; height: 1px;
    background: linear-gradient(90deg, rgba(255,255,255,0), rgba(255,255,255,.55), rgba(255,255,255,0));
  }
  .back-web {
    position: absolute; top: 284px; left: 0; width: 100%; text-align: center;
    color: var(--white); font-size: 16px; letter-spacing: 2.4px;
  }
</style>
</head>
<body>
<main class="canvas">

  <section class="card card-front" aria-label="Business card front">
    <div class="front-brand">
      <span class="brand-dot"></span>
      <span class="brand-name">Harborline Claim Partners</span>
    </div>

    <div class="holder">
      <p class="holder-name">MARCUS DELANEY</p>
      <p class="holder-role">CEO/Founder</p>
      <p class="holder-address">2140 Larkspur Court</p>
      <p class="holder-address">Evanston, Illinois 60201</p>
    </div>

    <div class="front-divider"></div>

    <ul class="contacts">
      <li>
        <svg viewBox="0 0 24 24" aria-hidden="true"><path d="M6.6 10.8a15.1 15.1 0 0 0 6.6 6.6l2.2-2.2a1 1 0 0 1 1-.25 11.4 11.4 0 0 0 3.6.57 1 1 0 0 1 1 1V20a1 1 0 0 1-1 1A17 17 0 0 1 3 4a1 1 0 0 1 1-1h3.5a1 1 0 0 1 1 1c0 1.25.2 2.45.57 3.57a1 1 0 0 1-.25 1z"/></svg>
        312 555 0184
      </li>
      <li>
        <svg viewBox="0 0 24 24" aria-hidden="true"><path d="M7 1h10a2 2 0 0 1 2 2v18a2 2 0 0 1-2 2H7a2 2 0 0 1-2-2V3a2 2 0 0 1 2-2zm0 3v14h10V4zm5 15.5a1.2 1.2 0 1 0 0 2.4 1.2 1.2 0 0 0 0-2.4z"/></svg>
        312 555 0427
      </li>
      <li>
        <svg viewBox="0 0 24 24" aria-hidden="true"><path d="M6 2h10l2 2v5H6zM3 10h18a2 2 0 0 1 2 2v7H1v-7a2 2 0 0 1 2-2zm3 5v7h12v-7zm2 2h8v1H8zm0 2h8v1H8z"/></svg>
        312 555 0639
      </li>
      <li>
        <svg viewBox="0 0 24 24" aria-hidden="true"><path d="M2 5h20v14H2zm2 2v.4l8 5.1 8-5.1V7zm0 2.8V17h16V9.8l-8 5.1z"/></svg>
        hello@harborlineclaims.com
      </li>
    </ul>

    <div class="web-band">www.harborlineclaims.com</div>
  </section>

  <section class="card card-back" aria-label="Business card back">
    <div class="back-brand">
      <span class="brand-dot"></span>
      <span class="brand-name">Harborline Claim Partners</span>
    </div>
    <div class="back-rule"></div>
    <p class="back-web">www.HarborlineClaimPartners.com</p>
  </section>

</main>
</body>
</html>
```